BildeVOLD buisnesscard

Hey :) I need a modern buisnesscard for my company BildeVOLD
It most have:
Dagligleder og Fotograf: Henrik Audun Strandvik

Mob: +4791264085
Epost: post@bildevold.example
Adresse: Kvernbakken9, 6040 Langevåg

Facbook and instagram logo with text BildeVOLD

BildeVOLD logo

It Company

```html
<!DOCTYPE html>
<html lang="no">
<head>
<meta charset="utf-8">
<title>BildeVOLD – visittkort</title>
<link href="https://fonts.googleapis.com/css2?family=Open+Sans:wght@400;600;700&display=swap" rel="stylesheet">
<style>
  :root {
    --bg: #3b3b3d;
    --blue: #1274bb;
    --pink: #c1427f;
    --ink: #2a2a2a;
    --white: #ffffff;
  }
  * { margin: 0; padding: 0; box-sizing: border-box; }
  html, body { width: 1200px; height: 1200px; overflow: hidden; }
  body {
    background: var(--bg);
    font-family: "Open Sans", Arial, sans-serif;
    display: flex;
    flex-direction: column;
    align-items: center;
    justify-content: center;
    gap: 70px;
  }
  .card {
    position: relative;
    width: 840px;
    height: 480px;
    overflow: hidden;
    box-shadow: 0 10px 24px rgba(0,0,0,.45);
  }
  .card--front {
    background: var(--blue);
    display: flex;
    align-items: center;
    justify-content: center;
  }
  .brand {
    display: flex;
    align-items: center;
    gap: 18px;
    font-weight: 700;
    letter-spacing: 1px;
  }
  .brand__mark { width: 40px; height: 40px; border-radius: 50%; }
  .card--front .brand { color: var(--white); font-size: 74px; }
  .card--front .brand__mark { background: var(--white); width: 52px; height: 52px; }

  .card--back { background: var(--white); }
  .card--back .brand {
    position: absolute; left: 120px; top: 150px;
    color: var(--blue); font-size: 60px;
  }
  .card--back .brand__mark { background: var(--pink); }

  .person {
    position: absolute; right: 70px; top: 70px;
    text-align: right;
  }
  .person__name { color: var(--blue); font-weight: 700; font-size: 26px; }
  .person__role { color: var(--pink); font-size: 20px; }
  .person-tab {
    position: absolute; right: 0; top: 74px;
    width: 42px; height: 60px; background: var(--blue);
  }

  .address {
    position: absolute; right: 60px; bottom: 96px;
    color: var(--ink); font-size: 20px;
  }

  .contacts {
    position: absolute; left: 120px; bottom: 60px;
    list-style: none; color: var(--ink); font-size: 20px; line-height: 30px;
  }
  .contacts li { display: flex; align-items: center; gap: 12px; }
  .contacts svg { width: 18px; height: 18px; fill: var(--blue); flex: none; }
  .social-box { width: 16px; height: 16px; background: var(--blue); border-radius: 3px; margin: 0 1px; flex: none; }

  .bands { position: absolute; left: 0; bottom: 0; width: 840px; height: 46px; }
</style>
</head>
<body>
  <section class="card card--front" aria-label="Forside">
    <div class="brand"><span class="brand__mark"></span>BildeVOLD</div>
  </section>

  <section class="card card--back" aria-label="Bakside">
    <div class="brand"><span class="brand__mark"></span>BildeVOLD</div>

    <div class="person-tab"></div>
    <div class="person">
      <p class="person__name">Henrik Audun Strandvik</p>
      <p class="person__role">Dagligleder og Fotograf</p>
    </div>

    <p class="address">Kvernbakken9, 6040 Langevåg</p>

    <ul class="contacts">
      <li>
        <svg viewBox="0 0 24 24" aria-hidden="true"><path d="M6.6 10.8c1.4 2.8 3.8 5.1 6.6 6.6l2.2-2.2c.3-.3.7-.4 1-.2 1.1.4 2.3.6 3.6.6.6 0 1 .4 1 1V20c0 .6-.4 1-1 1C10.6 21 3 13.4 3 4c0-.6.4-1 1-1h3.5c.6 0 1 .4 1 1 0 1.3.2 2.5.6 3.6.1.3 0 .7-.2 1z"/></svg>
        +4791264085
      </li>
      <li>
        <svg viewBox="0 0 24 24" aria-hidden="true"><path d="M2 5h20v14H2z M3 6l9 7 9-7" fill="none" stroke="#1274bb" stroke-width="2"/></svg>
        post@bildevold.example
      </li>
      <li><span class="social-box"></span>/BildeVOLD</li>
      <li><span class="social-box"></span>@BildeVOLD</li>
    </ul>

    <svg class="bands" viewBox="0 0 840 46" preserveAspectRatio="none" aria-hidden="true">
      <polygon points="0,28 560,28 548,46 0,46" fill="#1274bb"/>
      <polygon points="572,28 840,0 840,46 560,46" fill="#c1427f"/>
    </svg>
  </section>
</body>
</html>
```